Velmora Cabinets Letter Head and Email Signature

Hi
I would love a design package for a letterhead, email signature, even update my business card if you like if you can come up with a great idea for my new high end cabinet shop. Velmora Cabinets brings timeless craftsmanship to modern interiors, specializing in high end, custom cabinetry designed for architects and interior designers.

Target Market(s)

high end, luxury market

Industry/Entity Type

cabinet making

Requirements
Must have
• my colours of logo as the theme

```html
<!DOCTYPE html>
<html lang="en">
<head>
<meta charset="utf-8">
<title>Velmora Cabinets Stationery</title>
<link href="https://fonts.googleapis.com/css2?family=Montserrat:wght@400;500;600;700&display=swap" rel="stylesheet">
<style>
:root{
  --green:#4a7a4a;
  --band:#637f5e;
  --ink:#1b1b1b;
  --paper:#ffffff;
  --black:#000000;
  --backdrop:#4a2a1a;
  --label:#f4ece4;
  --faint:#d6e2d4;
}
*{margin:0;padding:0;box-sizing:border-box}
html,body{width:1200px;height:1200px;overflow:hidden}
body{background:var(--backdrop);font-family:"Montserrat",sans-serif;position:relative;color:var(--ink)}
.label{position:absolute;color:var(--label);font-size:15px;font-weight:400}
.label--letterhead{left:43px;top:17px}
.label--card{right:85px;top:77px}
.label--email{right:49px;top:851px}

.sheet{position:absolute;background:var(--paper);overflow:hidden}
.rule{position:absolute;top:0;bottom:0;width:1.5px;background:var(--ink)}
.band{position:absolute;left:0;right:0;background:var(--band);color:#fff;display:flex;align-items:center}
.brand{position:absolute;display:flex;align-items:center;color:var(--green);font-weight:600;white-space:nowrap}
.brand__mark{background:var(--green);flex:none}

.contact{list-style:none;position:absolute}
.contact li{display:flex;align-items:center;white-space:nowrap}
.icon{flex:none;fill:none;stroke:var(--green);stroke-width:1.6}

/* Letterhead */
.letterhead{left:43px;top:56px;width:604px;height:782px}
.letterhead .rule{left:18px}
.letterhead .brand{left:30px;top:40px;font-size:19px;gap:8px}
.letterhead .brand__mark{width:12px;height:12px}
.letterhead .contact{right:12px;top:24px;font-size:8px}
.letterhead .contact li{justify-content:flex-end;gap:6px;height:17px}
.letterhead .edge-mark{position:absolute;right:0;top:34px;width:2px;height:28px;background:var(--ink)}
.letterhead .watermark{position:absolute;right:18px;top:620px;font-size:38px;font-weight:600;color:var(--faint)}
.letterhead .band{top:734px;height:34px;padding-left:30px;font-size:14px}

/* Cards */
.card{left:802px;width:315px;height:178px}
.card--front{top:109px}
.card--front .rule{left:14px}
.card--front .brand{left:22px;top:27px;font-size:12px;gap:6px}
.card--front .brand__mark{width:8px;height:8px}
.person{position:absolute}
.person__name{color:var(--green);font-weight:700}
.person__role{font-weight:600}
.card--front .person{left:176px;top:16px}
.card--front .person__name{font-size:11.5px}
.card--front .person__role{font-size:6.5px;margin-top:2px}
.card--front .contact{left:176px;top:52px;font-size:7px}
.card--front .contact li{gap:6px;height:17px}
.card--front .band{top:122px;height:25px;padding-left:21px;font-size:7.5px;gap:6px}
.card--front .tagline{position:absolute;left:22px;top:158px;font-size:8.5px;font-weight:500}

.card--dark{background:var(--black)}
.card--back{top:307px}
.card--tag{top:504px}
.card--dark .brand{left:0;right:0;justify-content:center;font-size:22px;gap:10px}
.card--dark .brand__mark{width:16px;height:16px}
.card--back .brand{top:74px}
.card--tag .brand{top:52px}
.card--tag .tagline{position:absolute;left:0;right:0;top:121px;text-align:center;color:#fff;font-size:11px;font-weight:500}

/* Email signature */
.signature{left:602px;top:882px;width:550px;height:257px}
.signature .rule{left:25px}
.signature .brand{left:38px;top:36px;font-size:20px;gap:10px}
.signature .brand__mark{width:14px;height:14px}
.signature .person{left:268px;top:18px}
.signature .person__name{font-size:18px}
.signature .person__role{font-size:11px;margin-top:4px}
.signature .contact{left:268px;top:77px;font-size:12px}
.signature .contact li{gap:10px;height:25px}
.signature .band{top:167px;height:40px;padding-left:42px;font-size:15.5px;gap:12px}
.signature .tagline{position:absolute;left:43px;top:220px;font-size:15px;font-weight:600}
</style>
</head>
<body>

<svg width="0" height="0" style="position:absolute" aria-hidden="true">
  <defs>
    <symbol id="i-phone" viewBox="0 0 16 16"><path d="M4 2l2.5 3-1.5 1.5c.8 1.8 2.7 3.7 4.5 4.5L11 9.5 14 12l-1.5 2C8 14 2 8 2 3.5z"/></symbol>
    <symbol id="i-mail" viewBox="0 0 16 16"><rect x="2" y="4" width="12" height="9"/><path d="M2 4l6 5 6-5"/></symbol>
    <symbol id="i-social" viewBox="0 0 16 16"><circle cx="8" cy="8" r="5.5"/></symbol>
    <symbol id="i-pin" viewBox="0 0 16 16"><path d="M8 15s5-5.5 5-9A5 5 0 0 0 3 6c0 3.5 5 9 5 9z" fill="#fff" stroke="none"/><circle cx="8" cy="6" r="1.8" fill="#637f5e" stroke="none"/></symbol>
  </defs>
</svg>

<div class="label label--letterhead">Letterhead</div>
<div class="label label--card">Business Card</div>
<div class="label label--email">Email Signature</div>

<section class="sheet letterhead">
  <div class="rule"></div>
  <div class="brand"><span class="brand__mark"></span>Velmora Cabinets</div>
  <ul class="contact">
    <li>040 512 3360 <svg class="icon" width="10" height="10"><use href="#i-phone"/></svg></li>
    <li>info@velmoracabinets.com.au <svg class="icon" width="10" height="10"><use href="#i-mail"/></svg></li>
    <li>@velmora.cabinets <svg class="icon" width="10" height="10"><use href="#i-social"/></svg></li>
  </ul>
  <div class="edge-mark"></div>
  <div class="watermark">Velmora</div>
  <div class="band">Refined Craftmanship, Luxury Beauty</div>
</section>

<section class="sheet card card--front">
  <div class="rule"></div>
  <div class="brand"><span class="brand__mark"></span>Velmora Cabinets</div>
  <div class="person">
    <div class="person__name">Daniel Hartwell</div>
    <div class="person__role">Director Craftsman</div>
  </div>
  <ul class="contact">
    <li><svg class="icon" width="9" height="9"><use href="#i-phone"/></svg>040 512 3360</li>
    <li><svg class="icon" width="9" height="9"><use href="#i-mail"/></svg>info@velmoracabinets.com.au</li>
    <li><svg class="icon" width="9" height="9"><use href="#i-social"/></svg>@velmora.cabinets</li>
  </ul>
  <div class="band"><svg width="10" height="12"><use href="#i-pin"/></svg>445 Street Name, City Name Australia 20854</div>
  <div class="tagline">Refined Craftmanship, Luxury Beauty</div>
</section>

<section class="sheet card card--dark card--back">
  <div class="brand"><span class="brand__mark"></span>Velmora Cabinets</div>
</section>

<section class="sheet card card--dark card--tag">
  <div class="brand"><span class="brand__mark"></span>Velmora Cabinets</div>
  <div class="tagline">Refined Craftmanship, Luxury Beauty</div>
</section>

<section class="sheet signature">
  <div class="rule"></div>
  <div class="brand"><span class="brand__mark"></span>Velmora Cabinets</div>
  <div class="person">
    <div class="person__name">Daniel Hartwell</div>
    <div class="person__role">Director Craftsman</div>
  </div>
  <ul class="contact">
    <li><svg class="icon" width="15" height="15"><use href="#i-phone"/></svg>040 512 3360</li>
    <li><svg class="icon" width="15" height="15"><use href="#i-mail"/></svg>info@velmoracabinets.com.au</li>
    <li><svg class="icon" width="15" height="15"><use href="#i-social"/></svg>@velmora.cabinets</li>
  </ul>
  <div class="band"><svg width="18" height="24"><use href="#i-pin"/></svg>445 Street Name, City Name Australia 20854</div>
  <div class="tagline">Refined Craftmanship, Luxury Beauty</div>
</section>

</body>
</html>
```